Small Business Directory Site Requires a Professional Responsive Web Design

Small Business Directory and Coupon Site - we require a complete website design for a brand new responsive & mobile friendly website. We already have a coder who will professional code our website in Magento.

All PSD pages need to be professionally designed then uploaded into a sharedrive (i.e. like filecrate). Additionally, as I cannot pre-empt everything, please note that we may require a little more assistance once the files have been transferred (for example, in www.brightlane-listings.example if you hover your mouse on the search box you will see a pop up box. We want one of these too and I think that means there may be extra design work here)

We have some draft page sketches have been created (there are some minor changes we want to the sketches provided though); however, we require an excellent designer to add the creative touches to it to make it look professionally created. All artwork/font must be legal.

-------------------------
We like the look of the www.brightlane-listings.example and www. marlowfolio.example

For the headers, please consider a font similar to RNS camellia. We likes this style, but it is too thin for the headers...so we need a variation like this one. For the copy/general text font, something basic that marries well with the headers.

---------------------

Please be sure to also read the brief we wrote for the coder as this will help with better understanding our design requirements.

In total I believe we have about 50 pages. This includes all the little pages and most of the pop up boxes (but not the little help key boxes). For example, pages include...

1. Login (this is where customers log in and can edit, manage their profiles. This means that there are backend membership pages)
2. Mini Services (same look and feel as the business coupons)
3. Resource Centre
4. Join (this is where customers learn about the packages available to submit a directory listing, if they ‘buy’ a package (i.e. free, $25 or $150 package) then they can create their own directory listing)
5. Search the directory (customer can view all the categories and also search the directory)
6. Create a directory listing (this is where customers learn about the packages available to submit a directory listing, if they ‘buy’ a package (i.e. free, $25 or $150 package) then they can create their own directory listing)
7. Quote finder (also know as Get a Quote)
8. Coupons (customer go to the business coupon page and can view all current coupons/submit a coupon)
9. Submit a coupon (form)
10.Advertise with us (form)
11. Join the forum
12.Submit an article or video (form)
13. Affiliates (listing of affiliates we currently have)
14. Become an affiliate (form)
15. Case studies (customer can view the case studies we have in the resource centre)
16. Help Guides (customer can view the help guides we have in the resource centre)
17. About Us
18 .Contact Us (form)
19. Terms & Condition
20. Privacy Policy
21. Supporting City Councils
22. Site Map
23. Forgot password / login details
24. Homepage
25. If we hover over a few areas (i.e. search box, location field) it pops up with more information.
etc etc etc. . . there are more pages.

Please see our filecrate link for the draft mock up pages that I have created so far.

https://www.cloudtrunk.example/sh/qk72pmw4rtz8nd/KLMvbTq2fWndxPzs8Yh4ecRQu

We are in a rush! We'd like to get the majority of the artwork completed by the end of the month. Minor fixes/tweaks can occur thereafter.

Target Market(s)

Small Businesses (employees 0 - 50) located throughout Australia

Industry/Entity Type

Business

Font styles to use
Sans Serif

Requirements
Must have
• Professional. Artwork must be legal (cannot be cut and paste or taken off other websites, must be legally purchased and used).Must look contemporary, fresh, modern.

Absolutely must be a responsive site!
Nice to have
• original work, original photos, original art.

like modern, fresh photos that demonstrate innovation, growth, small business, Australian scenery, stability, goals/passion.
Should not have
• cut and paste graphics, illegal graphics, not purchased graphics.

```html
<!DOCTYPE html>
<html lang="en">
<head>
<meta charset="utf-8">
<title>BizLift Link – Helping Australian Small Businesses Grow</title>
<link href="https://fonts.googleapis.com/css2?family=Ubuntu:wght@400;500;700&display=swap" rel="stylesheet">
<style>
:root{
  --orange:#f26a10;
  --orange-dark:#d9570a;
  --black:#0b0b0b;
  --ink:#333;
  --grey-text:#8a8a8a;
  --light:#f3f3f3;
  --line:#dcdcdc;
  --white:#fff;
}
*{box-sizing:border-box;margin:0;padding:0}
html,body{width:805px;height:1200px;overflow:hidden}
body{position:relative;background:var(--light);font-family:"Ubuntu",sans-serif;color:var(--ink)}
.abs{position:absolute}

/* header */
.site-header{left:0;top:0;width:805px;height:64px;background:var(--black)}
.brand{left:93px;top:22px;display:flex;align-items:center;gap:6px}
.brand-mark{width:16px;height:16px;background:var(--orange)}
.brand-name{color:var(--orange);font-size:15px;font-weight:500}
.main-nav{right:89px;top:27px;display:flex;gap:17px}
.main-nav a{color:var(--white);font-size:8.5px;text-decoration:none;letter-spacing:.1px}

/* search */
.search-band{left:0;top:64px;width:805px;height:45px;background:#f6f6f6;border-bottom:1px solid #e4e4e4}
.field{height:28px;top:73px;background:var(--white);border:1px solid #dedede;font-size:9.5px;color:#aaa;padding:0 11px;line-height:26px}
.field-what{left:87px;width:240px}
.field-where{left:392px;width:236px}
.near{left:347px;top:79px;font-size:13px;color:#222}
.search-btn{left:644px;top:73px;width:73px;height:28px;background:var(--orange);color:var(--white);font-size:10px;font-weight:700;display:flex;align-items:center;justify-content:center;gap:5px}

/* hero */
.hero{left:0;top:109px;width:805px;height:402px;background:linear-gradient(180deg,#3b1f0a 0%,#b55a12 22%,#d9831c 32%,#6f3a12 48%,#3a2a20 60%,#5a4a40 78%,#2f2620 100%)}
.hero-title{left:87px;top:254px;color:var(--white);font-size:25px;font-weight:700;letter-spacing:.3px}
.hero-sub{left:87px;top:295px;color:var(--white);font-size:24px;font-weight:400;white-space:nowrap}
.join-btn{left:89px;top:345px;width:136px;height:33px;border-radius:17px;background:var(--orange);color:var(--white);font-size:12.5px;font-weight:700;display:flex;align-items:center;justify-content:center}
.arrow{top:296px}
.directory{left:525px;top:173px;width:192px;height:248px;border:2px solid var(--orange);background:rgba(205,205,205,.9)}
.directory h2{position:absolute;left:0;right:0;top:17px;text-align:center;font-size:15px;font-weight:700;color:#444}
.directory-card{left:17px;top:45px;width:154px;height:182px;background:#f7f7f7;text-align:center}
.directory-card p{font-size:8.6px;line-height:15.2px;color:#777;padding:13px 10px 0}
.listing-btn{left:10px;top:130px;width:134px;height:21px;border-radius:11px;background:#3a3a3a;color:var(--white);font-size:9px;display:flex;align-items:center;justify-content:center}
.card-dots{left:67px;top:160px;display:flex;gap:2px}
.card-dots span{width:10px;height:10px;border-radius:50%;background:#666}
.category-bar{left:0;top:461px;width:805px;height:50px;background:rgba(20,20,20,.82);display:flex;align-items:center;padding-left:95px;gap:16px}
.category-bar a{color:var(--white);font-size:7.3px;text-decoration:none}

/* community */
.section-title{left:0;top:554px;width:805px;text-align:center;color:var(--orange);font-size:21px;font-weight:700}
.col{top:600px;width:200px;text-align:center}
.col h3{font-size:12.5px;font-weight:500;color:#555;margin-bottom:12px}
.col p{font-size:7.6px;line-height:14px;color:var(--grey-text)}
.col-1{left:85px}.col-2{left:302px}.col-3{left:519px}
.media{top:710px;width:194px;height:130px;border:1px solid var(--line);background:var(--white);padding:2px}
.media-fill{width:100%;height:100%}
.m1{left:88px}.m2{left:306px}.m3{left:523px}
.case-img{background:linear-gradient(135deg,#e8e8e8,#9a9a9a 55%,#3a3a3a)}
.video-img{background:linear-gradient(90deg,#2b3f55,#6f8aa5 50%,#2f4258);position:relative}
.play{position:absolute;left:78px;top:47px}
.partner-card{display:flex;align-items:center;justify-content:center;color:#1b5aa0;font-size:22px;font-weight:500}
.media-link{top:854px;width:194px;text-align:center;color:var(--orange);font-size:10.5px;font-weight:700;text-decoration:underline}
.slide-dots{left:603px;top:859px;display:flex;gap:3px}
.slide-dots span{width:4px;height:4px;border-radius:50%;background:#666}
.slide-dots span.on{background:var(--orange)}

/* partner names */
.partners{left:0;top:908px;width:805px;height:77px;background:var(--white);border-top:1px solid #e2e2e2}
.partner-name{font-size:22px;font-weight:700;color:#333}

/* footer */
.site-footer{left:0;top:985px;width:805px;height:215px;background:var(--black)}
.foot-col{top:1018px}
.foot-col h4{color:var(--orange);font-size:9.5px;font-weight:400;margin-bottom:9px}
.foot-col a{display:block;color:#ddd;font-size:8.2px;text-decoration:none;line-height:17px}
.social{left:554px;top:1018px}
.social h4{color:var(--orange);font-size:9.5px;font-weight:400}
.social-icons{display:flex;gap:14px;margin-top:11px;margin-left:-4px}
.social-icons span{width:29px;height:29px;border-radius:50%;display:block}
.legal{left:0;top:1165px;width:805px;text-align:center;color:#ddd;font-size:7.6px;word-spacing:1px}
.legal span{margin:0 3px}
.code{left:749px;top:1166px;color:#ddd;font-size:7.6px}
</style>
</head>
<body>

<header class="site-header abs">
  <div class="brand abs"><span class="brand-mark"></span><span class="brand-name">BizLift Link</span></div>
  <nav class="main-nav abs">
    <a>LOGIN</a><a>JOIN</a><a>COUPONS</a><a>MINI SERVICES</a><a>GET A QUOTE</a><a>ADVERTISE</a><a>RESOURCE CENTRE</a>
  </nav>
</header>

<div class="search-band abs"></div>
<div class="field field-what abs">What are you looking for?</div>
<div class="near abs">Near</div>
<div class="field field-where abs">Where?</div>
<div class="search-btn abs">
  <svg width="12" height="12" viewBox="0 0 12 12"><circle cx="7.5" cy="4.5" r="3.3" fill="none" stroke="#fff" stroke-width="1.6"/><line x1="5" y1="7" x2="1" y2="11" stroke="#fff" stroke-width="2"/></svg>SEARCH
</div>

<section class="hero abs" role="img" aria-label="Sunset over the sea seen from a weathered wooden jetty"></section>
<svg class="arrow abs" style="left:22px" width="16" height="28" viewBox="0 0 16 28"><polyline points="14,2 3,14 14,26" fill="none" stroke="#ddd" stroke-width="3.5"/></svg>
<svg class="arrow abs" style="left:764px" width="16" height="28" viewBox="0 0 16 28"><polyline points="2,2 13,14 2,26" fill="none" stroke="#ddd" stroke-width="3.5"/></svg>
<h1 class="hero-title abs">LET US HELP YOU GROW</h1>
<p class="hero-sub abs">Australia’s Small Business Growth Hub</p>
<div class="join-btn abs">JOIN TODAY</div>

<aside class="directory abs">
  <h2>DIRECTORY</h2>
  <div class="directory-card abs">
    <p>Our small business directory is maintained to give members choice. We’re open to all businesses, regardless of your location, so long as they service Australian small businesses.</p>
    <div class="listing-btn abs">Create your free listing!</div>
    <div class="card-dots abs"><span></span><span></span></div>
  </div>
</aside>

<nav class="category-bar abs">
  <a>Banking</a><a>Finance &amp; Insurance</a><a>Marketing</a><a>Design</a><a>Photography</a><a>Video &amp; Print</a><a>Coaching &amp; Training</a><a>Technology</a><a>Legal</a><a>Administration</a><a>View All Categories</a>
</nav>

<h2 class="section-title abs">GET REAL SUPPORT FROM OUR COMMUNITY</h2>
<div class="col col-1 abs"><h3>How Did You Sort Your Business?</h3><p>Learn from Dana Morrow, a real small business owner. How she started her business and what are the most valuable resources for her right now.</p></div>
<div class="col col-2 abs"><h3>Why Go with BizLift Link?</h3><p>What small business owner can’t relate to the ongoing task of attracting new customers? Struggling with cash flow? Or how about not having enough time in the day? It’s obvious that small businesses suffer from a lack of support. And that’s where we come in.</p></div>
<div class="col col-3 abs"><h3>Become an Affiliate</h3><p>If you have a network of small businesses, let us help to create additional value for your members and make money for your network. Talk to us today about how we can help.</p></div>

<div class="media m1 abs"><div class="media-fill case-img" role="img" aria-label="Businessman in a suit reviewing a folder of documents at a desk"></div></div>
<div class="media m2 abs"><div class="media-fill video-img" role="img" aria-label="Video still of a person walking through a long glass corridor">
  <svg class="play" width="32" height="32" viewBox="0 0 32 32"><circle cx="16" cy="16" r="15" fill="rgba(0,0,0,.55)"/><polygon points="12,9 24,16 12,23" fill="#fff"/></svg>
</div></div>
<div class="media m3 abs"><div class="media-fill partner-card">Harbor Mutual</div></div>

<a class="media-link abs" style="left:88px">CASE STUDY</a>
<a class="media-link abs" style="left:306px">OUR WHITEBOARD VIDEO</a>
<div class="slide-dots abs"><span></span><span></span><span class="on"></span><span></span><span></span><span></span></div>

<section class="partners abs"></section>
<div class="partner-name abs" style="left:143px;top:934px">Granfield</div>
<div class="partner-name abs" style="left:346px;top:934px">Taskora</div>
<div class="partner-name abs" style="left:560px;top:934px">Orvane</div>

<footer class="site-footer abs"></footer>
<div class="foot-col abs" style="left:86px"><h4>SITE DIRECTORY</h4><a>News &amp; Articles</a><a>Find a Business</a><a>Maps &amp; Directions</a><a>White Pages</a><a>Mobile Apps</a><a>Reverse Phone Lookup</a></div>
<div class="foot-col abs" style="left:215px"><h4>RESOURCES</h4><a>Site Feedback</a><a>Contact us</a><a>Advertise with Us</a><a>Careers - We're Hiring</a><a>Engineering Blog</a></div>
<div class="foot-col abs" style="left:337px"><h4>CATEGORIES</h4><a>Chicago</a><a>Los Angeles</a><a>Philadelphia</a><a>Dallas</a><a>Louisville</a><a>Phoenix</a></div>
<div class="foot-col abs" style="left:442px"><h4>ABOUT</h4><a>Site Feedback</a><a>Contact us</a><a>Advertise with Us</a><a>Careers - We're Hiring</a><a>Engineering Blog</a><a>Legal | Terms of Service</a></div>
<div class="social abs"><h4>FOLLOW US OUR SOCIAL MEDIA LINKS</h4>
  <div class="social-icons">
    <span style="background:#2aa3e0" aria-label="Chirp"></span>
    <span style="background:#3b5998" aria-label="Folkbook"></span>
    <span style="background:#e8322c" aria-label="Snapgram"></span>
    <span style="background:#f39a1e" aria-label="Circleplus"></span>
  </div>
</div>
<p class="legal abs"><span>©2014 bizliftlink. All rights reserved</span><span>1-800-BIZ-LIFT</span><span>Conditions of Use</span><span>Privacy Policy</span><span>Help</span></p>
<p class="code abs">C4</p>

</body>
</html>
```